Quote Cards With KB May 2025 for Instagram

I would like to put these quotes over one of the pictures attached; Instagram (new size: 4:5 (1080 x 1350 pixels) One Quote per picture, and I want the quote to be bold or easy to read as well. I provided a few reference graphics that I really like as examples below. In very small letters at the bottom add @KBHarlowOnline

All of the pictures are attached; you can pick any photo and add one quote to it; but no stock photography

```html
<!DOCTYPE html>
<html lang="en">
<head>
<meta charset="utf-8">
<title>Quote Cards With KB – May 2025</title>
<link rel="stylesheet" href="https://fonts.googleapis.com/css2?family=Bebas+Neue&family=Archivo:wght@400;700;800&display=swap">
<style>
  :root {
    --board: #e5e5e6;
    --ink: #ffffff;
    --pink: #f2127f;
    --card-dark: #0b0b0b;
    --card-mid: #2a2a2a;
    --glass: rgba(255,255,255,0.08);
    --glass-line: rgba(255,255,255,0.45);
    --condensed: "Bebas Neue", "Oswald", sans-serif;
    --sans: "Archivo", "Helvetica Neue", Arial, sans-serif;
  }
  * { margin: 0; padding: 0; box-sizing: border-box; }
  html, body { width: 1200px; height: 1123px; overflow: hidden; background: var(--board); }
  .board { position: relative; width: 1200px; height: 1123px; }
  .card {
    position: absolute; width: 280px; height: 350px; overflow: hidden;
    background: linear-gradient(160deg, var(--card-mid), var(--card-dark) 70%);
    color: var(--ink); font-family: var(--sans);
  }
  .photo { position: absolute; }
  .t { position: absolute; line-height: 0.95; }
  .cond { font-family: var(--condensed); font-weight: 400; letter-spacing: 0; }
  .bold { font-weight: 800; }
  .pink { color: var(--pink); }
  .right { text-align: right; }
  .center { text-align: center; }
  .handle {
    position: absolute; font-family: var(--sans); font-weight: 700; font-size: 9px;
    display: flex; align-items: center; gap: 5px; color: var(--ink);
  }
  .handle .dot { width: 7px; height: 7px; border-radius: 50%; border: 1.3px solid var(--ink); }
  .handle .dot.pink-dot { border-color: var(--pink); }
  .glass { position: absolute; background: var(--glass); border: 1px solid var(--glass-line); border-radius: 4px; }
  .ghost {
    position: absolute; font-family: var(--condensed); font-size: 72px; line-height: 0.85;
    color: rgba(255,255,255,0.08); white-space: nowrap;
  }
</style>
</head>
<body>
<div class="board">

  <!-- Card: hormones screaming -->
  <section class="card" style="left:25px; top:206px; background:#050505;">
    <div class="photo" role="img" aria-label="Photo of KB in a black outfit, looking over her shoulder" style="left:20px; top:15px; width:110px; height:335px; background:radial-gradient(ellipse at 50% 45%, #2b2523, #050505 70%);"></div>
    <div class="t cond" style="left:124px; top:59px; font-size:19px;">TIRED. MOODY.<br>STUBBORN BELLY FAT.</div>
    <div class="t cond" style="left:124px; top:108px; font-size:25px;">YOUR HORMONES<br>ARE SCREAMING<br>FOR HELP<span class="pink">!</span></div>
    <div class="t cond pink" style="left:124px; top:188px; font-size:40px;">LET'S FIX<br>THAT</div>
    <div class="handle" style="left:124px; top:297px; font-size:10px;"><span class="dot"></span>@KBHarlowOnline</div>
  </section>

  <!-- Card: bloating -->
  <section class="card" style="left:25px; top:566px;">
    <div class="ghost" style="left:-6px; top:10px;">BLOATING.<br>MUFFIN TOP.<br>PUFFY WAISTLINE</div>
    <div class="photo" role="img" aria-label="Photo of KB smiling in a sparkly grey turtleneck" style="left:60px; top:25px; width:160px; height:200px; background:radial-gradient(ellipse at 50% 50%, #4a4546, transparent 70%);"></div>
    <div class="glass" style="left:29px; top:211px; width:221px; height:95px; background:rgba(20,20,20,0.8);"></div>
    <div class="t bold pink center" style="left:29px; top:224px; width:221px; font-size:12.5px;">BLOATING. MUFFIN TOP.<br>PUFFY WAISTLINE.</div>
    <div class="t center" style="left:29px; top:258px; width:221px; font-size:12px; line-height:1.05;">YOUR BODY'S SCREAMING<br>FOR A DIFFERENT KIND<br>OF FIX. HERE IT IS</div>
    <div class="handle" style="left:99px; top:322px;"><span class="dot"></span>@KBHarlowOnline</div>
  </section>

  <!-- Card: stubborn weight -->
  <section class="card" style="left:315px; top:27px;">
    <div class="photo" role="img" aria-label="Photo of KB from behind in an open-back black top" style="left:40px; top:20px; width:200px; height:330px; background:radial-gradient(ellipse at 45% 45%, #3a3231, transparent 72%);"></div>
    <div class="glass" style="left:120px; top:27px; width:145px; height:110px;"></div>
    <div class="t cond right" style="left:120px; top:38px; width:133px; font-size:33px;">THAT<br>STUBBORN<br>WEIGHT?</div>
    <div class="t cond" style="left:19px; top:194px; font-size:29px;">IT'S NOT<br><span class="pink">YOUR FAULT</span></div>
    <div class="t" style="left:19px; top:251px; font-size:10.5px; line-height:1.1;">YOUR HORMONES<br>ARE TO BLAME &amp;<br>YOU'RE NOT ALONE;</div>
    <div class="t bold" style="left:19px; top:288px; font-size:15px;">BUT THERE<br>IS A FIX.</div>
    <div class="handle" style="left:175px; top:320px;"><span class="dot"></span>@KBHarlowOnline</div>
  </section>

  <!-- Card: stubborn belly fat after 40 -->
  <section class="card" style="left:315px; top:386px;">
    <div class="photo" role="img" aria-label="Photo of KB in a sheer striped black top, blowing a kiss" style="left:105px; top:0; width:175px; height:350px; background:radial-gradient(ellipse at 55% 45%, #3d3838, transparent 72%);"></div>
    <div class="t bold" style="left:19px; top:52px; font-size:19px;">THE<br>STUBBORN<br>BELLY FAT<br>AFTER 40?</div>
    <div class="t cond" style="left:19px; top:150px; font-size:20px; line-height:0.92;">IT'S NOT ABOUT<br>CALORIES IT'S<br>ABOUT YOUR<br>HORMONES.</div>
    <div class="t cond" style="left:19px; top:225px; font-size:46px; line-height:0.85;">HERE IS<br>THE FIX!</div>
    <div class="handle" style="left:19px; top:321px;"><span class="dot"></span>@KBHarlowOnline</div>
  </section>

  <!-- Card: flat tummy -->
  <section class="card" style="left:315px; top:746px;">
    <div class="photo" role="img" aria-label="Photo of KB smiling in a long magenta wrap dress" style="left:140px; top:15px; width:140px; height:335px; background:linear-gradient(180deg, #3a2a33, #a0136b 55%, #5a0d3e);"></div>
    <div class="t cond" style="left:24px; top:36px; font-size:30px;">FLAT TUMMY<br>IN YOUR 40s?</div>
    <div class="t cond" style="left:24px; top:96px; font-size:44px; line-height:0.88;">IT'S STILL<br><span class="pink">POSSIBLE!</span></div>
    <div class="glass" style="left:15px; top:179px; width:117px; height:111px; background:rgba(15,15,15,0.7);"></div>
    <div class="t" style="left:25px; top:187px; font-size:13px; line-height:1.05;">Comment<br><b class="pink">"BYE BELLY"</b><br>To get the<br><span class="cond" style="font-size:17px;">10 SECRETS</span><br>to a Flatter<br>Tummy</div>
    <div class="handle" style="left:25px; top:314px;"><span class="dot pink-dot"></span>@KBHarlowOnline</div>
  </section>

  <!-- Card: it's hormonal -->
  <section class="card" style="left:605px; top:27px;">
    <div class="photo" role="img" aria-label="Photo of KB smiling in a black mesh top and black pants, hand on hip" style="left:0; top:15px; width:160px; height:335px; background:radial-gradient(ellipse at 50% 45%, #3a3535, transparent 72%);"></div>
    <div class="t right" style="right:29px; top:35px; font-size:23px; line-height:1;">Your Belly<br>Isn't Fat...</div>
    <div class="t bold right" style="right:29px; top:88px; font-size:22px; line-height:1;">It's<br>Hormonal</div>
    <div class="t cond right" style="right:29px; top:142px; font-size:33px; line-height:0.85;">AND HERE'S<br>HOW TO <span class="pink">FIX IT</span></div>
    <div class="t right" style="right:29px; top:214px; font-size:16px; line-height:1.15;">Comment<br><b class="pink" style="font-size:19px;">"HORMONES"</b><br>if nothing is<br>working.</div>
    <div class="handle" style="left:170px; top:315px;"><span class="dot pink-dot"></span>@KBHarlowOnline</div>
  </section>

  <!-- Card: 90-day plan -->
  <section class="card" style="left:605px; top:386px;">
    <div class="t cond pink center" style="left:0; top:22px; width:280px; font-size:44px;">90-DAY PLAN</div>
    <div class="t center" style="left:0; top:66px; width:280px; font-size:20px; line-height:1;">HELPED WOMEN OVER<br>40 SLIM DOWN</div>
    <div class="t center" style="left:0; top:110px; width:280px; font-size:16px; line-height:1.05;">Get a Tiny Waist and Feel<br>Sexy again. <b class="pink">You're Next</b>.</div>
    <div class="photo" role="img" aria-label="Photo of KB in a white cropped sweater, pointing up with both hands" style="left:40px; top:140px; width:200px; height:165px; background:radial-gradient(ellipse at 50% 60%, #cfcaca, #4a4646 55%, transparent 75%);"></div>
    <div class="handle" style="left:88px; top:315px; font-size:10px;"><span class="dot pink-dot"></span>@KBHarlowOnline</div>
  </section>

  <!-- Card: skinny secret -->
  <section class="card" style="left:605px; top:746px; background:linear-gradient(180deg,#3a3a3a,#111 85%);">
    <div class="photo" role="img" aria-label="Photo of KB courtside in a pink sparkly top holding a basketball, crowd behind" style="left:0; top:0; width:280px; height:230px; background:radial-gradient(ellipse at 40% 55%, #6a3c57, #3a3a3a 55%, transparent 85%);"></div>
    <div class="glass" style="left:158px; top:-2px; width:123px; height:99px; background:rgba(40,40,40,0.7);"></div>
    <div class="t center" style="left:158px; top:14px; width:123px; font-size:15px; line-height:1.05;">Comment<br><b class="pink" style="font-size:18px;">"SKINNY"</b><br>To Get The<br>Exact Plan</div>
    <div class="glass" style="left:29px; top:210px; width:222px; height:83px; background:rgba(10,10,10,0.8);"></div>
    <div class="t center" style="left:29px; top:224px; width:222px; font-size:12px; line-height:1.05;">THIS IS THE SECRET WOMEN<br>OVER 40 ARE USING TO<br>GET SNATCHED</div>
    <div class="t bold pink center" style="left:29px; top:269px; width:222px; font-size:13.5px;">WITHOUT STARVING</div>
    <div class="handle" style="left:100px; top:316px;"><span class="dot pink-dot"></span>@KBHarlowOnline</div>
  </section>

  <!-- Card: right things -->
  <section class="card" style="left:895px; top:206px;">
    <div class="photo" role="img" aria-label="Photo of KB in a sheer black top and jeans in front of a night city view" style="left:0; top:0; width:280px; height:350px; background:radial-gradient(ellipse at 30% 50%, #3b3838, #151515 55%, #070707);"></div>
    <div class="t cond" style="left:117px; top:52px; font-size:28px; line-height:0.9;">YOU'RE DOING<br>ALL THE<br>"RIGHT <span class="pink">THINGS</span>"</div>
    <div class="t bold" style="left:134px; top:136px; font-size:12px;">BUT YOUR BELLY<br>WON'T GO DOWN?</div>
    <div class="t cond" style="left:117px; top:200px; font-size:34px; line-height:0.88;">HERE'S WHAT<br>YOU HAVEN'T<br><span class="pink">TRIED</span>!</div>
    <div class="handle" style="left:117px; top:311px;"><span class="dot pink-dot"></span>@KBHarlowOnline</div>
  </section>

  <!-- Card: what worked in your 30s -->
  <section class="card" style="left:895px; top:566px;">
    <div class="photo" role="img" aria-label="Photo of KB in a pink sparkly fitted dress, hand on hip" style="left:10px; top:20px; width:130px; height:330px; background:radial-gradient(ellipse at 50% 55%, #a8667f, #3a2f33 50%, transparent 75%);"></div>
    <div class="t" style="left:112px; top:50px; font-size:19px; line-height:0.98;">WHAT WORKED<br>IN YOUR 30S<br>WON'T WORK<br>NOW</div>
    <div class="t cond" style="left:112px; top:128px; font-size:30px; line-height:0.88;">HERE'S WHAT<br><span class="pink">ACTUALLY DOES</span></div>
    <div class="t cond" style="left:143px; top:187px; font-size:33px; line-height:0.88;">DROP 30<br>POUNDS IN<br><span class="pink">3 MONTHS</span></div>
    <div class="handle" style="left:143px; top:302px;"><span class="dot pink-dot"></span>@KBHarlowOnline</div>
  </section>

</div>
</body>
</html>
```